SOLVE Study flyer

I need help designing a flyer for a research study that will include brain imaging in adolescents. The info is in the attached document. The study is called the Sequoia Outlook Lantern Valley Echo (SOLVE) study. Ideally this would be returned as a document that I can edit in the future as we will have several new recruitment phases (different age groups, etc. I also would love to have a logo designed as part of this project, but I recognize that might be a separate design request.

```html
<!DOCTYPE html>
<html lang="en">
<head>
<meta charset="utf-8">
<title>SOLVE Study – Recruitment Flyer</title>
<link href="https://fonts.googleapis.com/css2?family=Figtree:wght@400;500;600;700;800&display=swap" rel="stylesheet">
<style>
  :root {
    --brand-blue: #1f5b8c;
    --ink: #1c1c1c;
    --band-green: #d6e7d8;
    --cream: #fdf3dd;
    --cream-deep: #fbe9c2;
    --panel-white: #ffffff;
    --sky: #d7eaf5;
    --leaf: #5f9a72;
    --frame: #e2e2e2;
  }
  * { box-sizing: border-box; margin: 0; padding: 0; }
  html, body { width: 929px; height: 1200px; overflow: hidden; background: #ffffff; }
  body { font-family: "Figtree", "Helvetica Neue", Arial, sans-serif; color: var(--ink); }

  .flyer { position: relative; width: 929px; height: 1200px; background: #ffffff; border: 1px solid var(--frame); overflow: hidden; }

  /* Header */
  .brand { position: absolute; left: 70px; top: 62px; }
  .brand-name { font-size: 68px; font-weight: 800; color: var(--brand-blue); letter-spacing: 1px; line-height: 1; }
  .brand-full { margin-top: 14px; font-size: 19px; font-weight: 500; line-height: 1.3; color: var(--ink); width: 280px; }
  .brand-mark { position: absolute; left: 372px; top: 78px; width: 96px; height: 96px; border-radius: 50%; background: var(--sky); }

  .study-title { position: absolute; left: 500px; top: 48px; width: 400px; text-align: center; }
  .study-title .kicker { font-size: 30px; font-weight: 700; color: var(--brand-blue); line-height: 1.2; }
  .study-title .headline { font-size: 31px; font-weight: 700; color: var(--ink); line-height: 1.28; margin-top: 4px; }

  /* Green band */
  .audience-band { position: absolute; left: 19px; top: 242px; width: 891px; height: 233px; background: var(--band-green); }
  .audience-question { position: absolute; left: 67px; top: 26px; font-size: 35px; font-weight: 700; line-height: 1.3; width: 400px; }
  .audience-sub { position: absolute; left: 67px; top: 140px; font-size: 27px; font-weight: 700; line-height: 1.3; width: 420px; }
  .audience-art { position: absolute; right: 8px; top: 4px; width: 390px; height: 229px; border-radius: 120px 120px 0 0; background: linear-gradient(180deg, #dbeaf3 0%, #cfe2ea 55%, #e6d2b8 100%); }

  /* Lower area */
  .details-area { position: absolute; left: 19px; top: 475px; width: 891px; height: 710px; background: var(--cream); }
  .cream-swell { position: absolute; left: 0; top: 0; }
  .details-panel { position: absolute; left: 32px; top: 0; width: 830px; height: 568px; background: var(--panel-white); border-left: 2px solid var(--brand-blue); border-right: 2px solid var(--brand-blue); }
  .leaf-sprig { position: absolute; left: 775px; top: 110px; width: 116px; height: 160px; border-radius: 60px 10px 60px 10px; background: linear-gradient(160deg, #a9cdb0, #6fa381); opacity: 0.55; }

  .section { position: absolute; left: 52px; }
  .section-heading { display: flex; align-items: center; gap: 12px; font-size: 27px; font-weight: 700; line-height: 1; }
  .section-heading::before { content: ""; width: 8px; height: 8px; border-radius: 50%; background: var(--brand-blue); }
  .section-body { margin-left: 21px; margin-top: 12px; font-size: 20.5px; font-weight: 500; line-height: 1.42; width: 700px; }

  .overview { top: 38px; }
  .involves { top: 163px; }
  .eligibility { top: 400px; }

  .task-list { list-style: none; margin-top: 14px; }
  .task { display: flex; align-items: flex-start; gap: 14px; font-size: 20.5px; font-weight: 500; line-height: 1.42; width: 720px; margin-bottom: 12px; }
  .task-icon { flex: 0 0 50px; height: 50px; }
  .task:nth-child(1) .task-text { padding-top: 0; }
  .task:nth-child(2) .task-text { padding-top: 12px; }

  .criteria { list-style: none; margin-left: 45px; margin-top: 12px; }
  .criteria li { position: relative; padding-left: 20px; font-size: 20.5px; font-weight: 500; line-height: 1.42; }
  .criteria li::before { content: ""; position: absolute; left: 0; top: 12px; width: 6px; height: 6px; border-radius: 50%; background: var(--ink); }

  /* Contact */
  .contact-box { position: absolute; left: 27px; top: 575px; width: 836px; height: 100px; border: 2px solid var(--brand-blue); border-radius: 16px; background: var(--sky); text-align: center; padding-top: 36px; font-size: 20.5px; font-weight: 500; line-height: 1.45; }
  .compensation { position: absolute; left: 214px; top: 538px; width: 462px; height: 46px; border-radius: 12px; background: var(--brand-blue); color: #ffffff; font-size: 27px; font-weight: 700; display: flex; align-items: center; justify-content: center; }
</style>
</head>
<body>
<main class="flyer">

  <header>
    <div class="brand">
      <div class="brand-name">SOLVE</div>
      <div class="brand-full">Sequoia Outlook Lantern Valley Echo</div>
    </div>
    <div class="brand-mark" aria-hidden="true"></div>

    <div class="study-title">
      <div class="kicker">SOLVE Study:</div>
      <h1 class="headline">Understanding Brain Development and Worry in Teens</h1>
    </div>
  </header>

  <section class="audience-band">
    <h2 class="audience-question">Are you the parent of a child age 10-17?</h2>
    <p class="audience-sub">Do they worry or overthink negative emotions?</p>
    <div class="audience-art" role="img" aria-label="Illustration of three thoughtful teenage girls with thought bubbles showing brains and puzzle pieces"></div>
  </section>

  <section class="details-area">
    <svg class="cream-swell" width="891" height="710" viewBox="0 0 891 710" aria-hidden="true">
      <path d="M560 520 C 640 470, 700 340, 891 300 L 891 710 L 560 710 Z" fill="var(--cream-deep)"/>
    </svg>

    <div class="details-panel">
      <div class="section overview">
        <h3 class="section-heading">Study Overview</h3>
        <p class="section-body">Researchers are seeking girls ages 10-17 for a study about brain activity, emotions, decision-making, and their relationship to puberty, anxiety, and depression.</p>
      </div>

      <div class="section involves">
        <h3 class="section-heading">Participation Involves</h3>
        <ul class="task-list">
          <li class="task">
            <svg class="task-icon" viewBox="0 0 50 50" aria-hidden="true">
              <rect x="5" y="14" width="10" height="18" rx="5" fill="#7fb79a" stroke="var(--brand-blue)" stroke-width="1.6"/>
              <path d="M3 28 a7 7 0 0 0 14 0 M10 35 v8 M5 43 h10" fill="none" stroke="var(--brand-blue)" stroke-width="1.6"/>
              <rect x="20" y="4" width="26" height="17" rx="4" fill="#bfe0ef" stroke="var(--brand-blue)" stroke-width="1.6"/>
              <path d="M25 21 l-3 6 l8 -6" fill="#bfe0ef" stroke="var(--brand-blue)" stroke-width="1.6"/>
              <path d="M25 10 h16 M25 15 h12" stroke="var(--brand-blue)" stroke-width="1.6"/>
            </svg>
            <span class="task-text">One 1-hour interview (online or in-person) discussing thoughts.</span>
          </li>
          <li class="task">
            <svg class="task-icon" viewBox="0 0 50 50" aria-hidden="true">
              <rect x="6" y="6" width="34" height="40" rx="3" fill="#eef6fb" stroke="var(--brand-blue)" stroke-width="1.8"/>
              <rect x="16" y="3" width="14" height="7" rx="2" fill="var(--brand-blue)"/>
              <path d="M12 18 h18 M12 24 h18 M12 30 h14 M12 37 h8" stroke="var(--brand-blue)" stroke-width="1.6"/>
              <path d="M46 16 L32 38 l-3 4 l1 -5 L44 15 Z" fill="#7fb79a" stroke="var(--brand-blue)" stroke-width="1.4"/>
            </svg>
            <span class="task-text">Online questionnaires (parent and child).</span>
          </li>
          <li class="task">
            <svg class="task-icon" viewBox="0 0 50 50" aria-hidden="true">
              <rect x="4" y="4" width="40" height="42" rx="12" fill="#bfe0ef" stroke="var(--brand-blue)" stroke-width="1.8"/>
              <circle cx="24" cy="22" r="10" fill="#ffffff" stroke="var(--brand-blue)" stroke-width="1.8"/>
              <rect x="14" y="30" width="20" height="8" rx="2" fill="#7fb79a" stroke="var(--brand-blue)" stroke-width="1.4"/>
              <path d="M8 42 h32" stroke="var(--brand-blue)" stroke-width="1.8"/>
            </svg>
            <span class="task-text">One 2-hour visit with an MRI scan, puberty stage questions, and a small hair sample.</span>
          </li>
        </ul>
      </div>

      <div class="section eligibility">
        <h3 class="section-heading">Eligibility</h3>
        <ul class="criteria">
          <li>Age 10-17</li>
          <li>Tendency to worry or overthink negative thoughts</li>
          <li>No diagnosis of psychosis, learning problems, or autism</li>
        </ul>
      </div>
    </div>

    <div class="leaf-sprig" role="img" aria-label="Decorative green leafy sprig"></div>

    <div class="contact-box">
      <p>Interested in participating? Want more information? Please contact us!</p>
      <p>Email: solvestudy@lanternvalley.org</p>
    </div>
    <div class="compensation">Compensation up to $140</div>
  </section>

</main>
</body>
</html>
```